Business Intelligence Application - Reporting Menu and Report Criteria Design

Looking for a fresh, effective and user friendly view for the menu structure and reporting criteria screen format for a business reporting application. Initial format completed, content structure is in place, but we need the 'wow' design.. as its a serious professional report/BI tool it has to fall within certain guidelines for clarity and graphics..but we want it to be slick, friendly, great user experience. There is a large amount of complex content to fit into a small space and we need it to be very inviting, modern and intuitive.. If interested, please review the attachment. We have live screens in operation, but feel these could be improved and looking forward to seeing what great creative suggestions could be made. Please review work done to date in the attached.. We are not looking for a total re-design of everything, all the basic business content/structure is there.. but tell us what we could do to improve this in terms of graphic design... particularly the criteria screens.. thanks!
Updates

Reason: Need a few more days to review designs - thanks for all submissions so far, we will make a selection shortly.

Target Market(s)

Business analysts, hotel operations teams, finance analysts hospitality industry

Industry/Entity Type

Hospitality

Coding

Coded - Design and coding required

Number of Pages Required

4 page

Font styles to use
Sans Serif
Other font styles liked:
• Candara, please see example in deck

Colors
3276b5
3176b5
0255a3
85acd3
33a6d7
cee9f5
85cae6

Requirements
Must have
• sharp clear, logical menu structure, (currently it has 'clicks to sub-menus, we need hover over, slide to sub-menus..) colour, styling.. and most focus on revision of criteria.. right now is somewhat heavy, cumbersome.. keep colour and friendly intuitive process steps.. its heavy analytical stuff.. best of luck!
Should not have
• No grey fonts on white or grey screens! many business apps are not readable or sharp.. or fonts are too small.. colourless, so please avoid that.. see our deck - sharp dark (navy) or black fonts on white, or light shading..

```html
<!DOCTYPE html>
<html lang="en">
<head>
<meta charset="utf-8">
<title>Amber Coast Hotels &amp; Suites — Reporting</title>
<link rel="stylesheet" href="https://fonts.googleapis.com/css2?family=Cabin:wght@400;500;600&display=swap">
<style>
  :root {
    --header-bg: #d2e9f5;
    --brand: #33a6d7;
    --button: #33a6d7;
    --menu: #33a6d7;
    --menu-active: #85cae6;
    --menu-divider: rgba(255,255,255,0.35);
    --ink: #111a24;
    --dot: #3276b5;
    --border: #9a9ea3;
    --white: #ffffff;
  }
  * { box-sizing: border-box; margin: 0; padding: 0; }
  html, body { width: 1200px; height: 506px; overflow: hidden; background: var(--white); }
  body { position: relative; font-family: "Cabin", "Candara", sans-serif; color: var(--ink); }

  .topbar { position: absolute; left: 0; top: 0; width: 1200px; height: 60px; background: var(--header-bg); }
  .brand { position: absolute; left: 47px; top: 14px; display: flex; align-items: center; gap: 9px; }
  .brand-mark { width: 30px; height: 30px; border-radius: 50%; background: var(--brand); }
  .brand-name { font-size: 19px; font-weight: 500; color: var(--brand); letter-spacing: -0.1px; }
  .greeting, .today { position: absolute; top: 21px; font-size: 12.5px; font-weight: 500; }
  .greeting { left: 554px; }
  .today { left: 667px; }
  .top-button { position: absolute; top: 12px; height: 37px; background: var(--button); color: var(--white);
    font-size: 12px; font-weight: 600; letter-spacing: 0.3px; display: flex; align-items: center; justify-content: center; }
  .top-button.intel { left: 832px; width: 85px; }
  .top-button.planning { left: 954px; width: 108px; }
  .icon { position: absolute; top: 17px; }
  .icon.alerts { left: 1084px; }
  .icon.share { left: 1125px; }

  .main-nav { position: absolute; left: 47px; top: 89px; display: flex; align-items: center; font-size: 12.8px; font-weight: 500; }
  .main-nav .sep { width: 3px; height: 3px; border-radius: 50%; background: var(--dot); margin: 0 9px; }

  .property-search { position: absolute; left: 775px; top: 81px; width: 376px; height: 37px; border: 1px solid var(--border);
    display: flex; align-items: center; padding-left: 16px; font-size: 11px; letter-spacing: 0.2px; }
  .property-search svg { position: absolute; right: 11px; top: 11px; }

  .search-menu { position: absolute; left: 775px; top: 142px; width: 163px; background: var(--menu);
    box-shadow: 0 2px 6px rgba(0,0,0,0.15); }
  .search-menu::before { content: ""; position: absolute; left: 12px; top: -7px; border-left: 7px solid transparent;
    border-right: 7px solid transparent; border-bottom: 7px solid var(--menu); }
  .menu-item { height: 33.6px; display: flex; align-items: center; justify-content: space-between; padding: 0 11px;
    color: var(--white); font-size: 10.6px; border-bottom: 1px solid var(--menu-divider); }
  .menu-item:last-child { border-bottom: 0; }
  .menu-item.active { background: var(--menu-active); }
  .arrow-right { width: 0; height: 0; border-top: 4px solid transparent; border-bottom: 4px solid transparent; border-left: 4px solid var(--white); }
  .arrow-down { width: 0; height: 0; border-left: 4px solid transparent; border-right: 4px solid transparent; border-top: 4px solid var(--white); }

  .division-menu { position: absolute; left: 938px; top: 242px; width: 164px; background: var(--menu);
    box-shadow: 0 2px 6px rgba(0,0,0,0.18); }
  .division-menu .menu-item { padding: 0 13px 0 17px; height: 32.5px; }
  .division-menu .menu-item.group { box-shadow: 0 2px 4px rgba(0,0,0,0.18); position: relative; }
</style>
</head>
<body>
  <header class="topbar">
    <div class="brand"><span class="brand-mark"></span><span class="brand-name">Amber Coast Hotels &amp; Suites</span></div>
    <span class="greeting">Welcome Admin</span>
    <span class="today">Tuesday October 04.2017</span>
    <span class="top-button intel">INTEL</span>
    <span class="top-button planning">PLANNING</span>
    <svg class="icon alerts" width="26" height="24" viewBox="0 0 26 24" fill="none" stroke="#111a24" stroke-width="1.3" aria-label="Alerts">
      <path d="M8 17 V11 a5 5 0 0 1 10 0 V17 l2 2 H6 z"/>
      <path d="M11 20 a2 2 0 0 0 4 0"/>
      <circle cx="13" cy="4.5" r="1.3"/>
      <path d="M4 8 a7 7 0 0 0 0 7 M22 8 a7 7 0 0 1 0 7"/>
    </svg>
    <svg class="icon share" width="28" height="22" viewBox="0 0 28 22" fill="none" stroke="#111a24" stroke-width="1.4" aria-label="Share">
      <path d="M18 3 L26 8.5 L18 14 V10.5 C12 10.5 9 12 6 16 C7 10 10 7 18 6.5 z"/>
      <path d="M14 20 H2 V8 H6"/>
    </svg>
  </header>

  <nav class="main-nav">
    <span>Admin</span><span class="sep"></span>
    <span>Management</span><span class="sep"></span>
    <span>Rooms Performance</span><span class="sep"></span>
    <span>Revenue Summary</span><span class="sep"></span>
    <span>Demand &amp; Risk</span><span class="sep"></span>
    <span>Inventory Analysis</span><span class="sep"></span>
    <span>Placeholder</span>
  </nav>

  <div class="property-search">PROPERTY SEARCH
    <svg width="15" height="15" viewBox="0 0 15 15" fill="none" stroke="#111a24" stroke-width="1.3"><circle cx="6.5" cy="6.5" r="5"/><path d="M10.2 10.2 L14 14"/></svg>
  </div>

  <div class="search-menu">
    <div class="menu-item">Property Name <span class="arrow-right"></span></div>
    <div class="menu-item">Property ID</div>
    <div class="menu-item">Product Type</div>
    <div class="menu-item active">All Division <span class="arrow-right"></span></div>
    <div class="menu-item">All Region</div>
    <div class="menu-item">All Area</div>
  </div>

  <div class="division-menu">
    <div class="menu-item group">North America <span class="arrow-down"></span></div>
    <div class="menu-item">Southwest USA</div>
    <div class="menu-item group">Northeast USA <span class="arrow-down"></span></div>
    <div class="menu-item">Coral Bay Hotel</div>
    <div class="menu-item">Midtown Harbor Hotel</div>
  </div>
</body>
</html>
```